Willow Fen Racquet Club (Tennis Country Club)

Racquet and Tennis Country Club in Florida.
This web sight is needed for a Privet Tennis club located in Deerfield Beach city in Florida, USA.
We have 10 clay tennis courts and 2 hard tennis courts, small and cozy swimming pool and a clubhouse (see attached pictures) Attached pictures are for information only because we are under a reconstruction.
Updates

I haven't received any source files and web converted files neither!

Target Market(s)

Adult members, Kids members, Tennis players

Coding

Coded - Design and coding required

Number of Pages Required

3 page

Requirements
Must have
• Logo colors (see attached file)

```html
<!DOCTYPE html>
<html lang="en">
<head>
<meta charset="utf-8">
<title>Willow Fen Racquet Club</title>
<link href="https://fonts.googleapis.com/css2?family=Josefin+Sans:wght@400;600;700&family=Roboto:ital,wght@0,400;0,500;0,700;1,400&display=swap" rel="stylesheet">
<style>
:root{
  --green:#1f6b3d;
  --green-dark:#17552f;
  --ink:#222;
  --muted:#555;
  --line:#e3e3e3;
  --footer:#1b1b1b;
  --white:#fff;
}
*{margin:0;padding:0;box-sizing:border-box}
html,body{width:1200px;height:3468px;overflow:hidden}
body{position:relative;font-family:'Roboto',sans-serif;color:var(--ink);background:#fff}
.abs{position:absolute}
.heading{font-family:'Josefin Sans',sans-serif;font-weight:700;text-transform:uppercase}
.body-text{font-size:13px;line-height:25px;color:var(--muted)}

/* hero */
.hero{left:0;top:0;width:1200px;height:640px}
.hero-bg{position:absolute;left:0;top:0}
.brand{left:97px;top:34px;display:flex;flex-direction:column;align-items:center;color:#fff}
.brand-mark{width:44px;height:44px;border:3px solid #fff;border-radius:50%}
.brand-name{font-family:'Josefin Sans',sans-serif;font-weight:600;font-size:20px;margin-top:6px}
.nav{right:82px;top:56px;display:flex;gap:30px;align-items:center}
.nav a{color:#fff;text-decoration:none;font-size:14px;font-weight:500}
.nav .search{display:block}
.hero-title{left:97px;top:218px;color:#fff;font-size:56px;line-height:66px}
.hero-ghost{left:97px;top:352px;font-size:86px;color:rgba(255,255,255,.18)}
.dots{left:1142px;top:270px;display:flex;flex-direction:column;gap:17px}
.dots span{width:18px;height:18px;border:2px solid #fff;border-radius:50%}
.dots span.on{background:#fff}

.weather{left:97px;top:458px;width:286px;height:286px;border-radius:50%;background:var(--green);border:6px solid #fff;box-shadow:0 4px 14px rgba(0,0,0,.25);color:#fff;text-align:center}
.weather .city{margin-top:52px;font-size:30px}
.weather .country{font-size:16px;margin-top:4px}
.weather .date{font-size:15px;margin-top:14px}
.weather .temp{position:absolute;left:52px;top:168px;font-size:40px;font-weight:700}
.weather .range{position:absolute;left:54px;top:216px;font-size:11px}
.weather svg{position:absolute;left:170px;top:170px}

/* welcome */
.welcome-title{left:97px;top:800px;font-size:33px;color:#111}
.welcome-text{left:97px;top:866px;width:518px;text-align:justify}
.btn{display:inline-flex;align-items:center;gap:8px;background:var(--green);color:#fff;font-size:14px;font-weight:700;text-transform:uppercase;border-radius:24px;text-decoration:none}
.welcome-btn{left:97px;top:1046px;height:44px;padding:0 24px}
.video{left:677px;top:807px;width:423px;height:280px;border:6px solid #fff;box-shadow:0 0 0 1px var(--line);background:linear-gradient(160deg,#7aa86a 0%,#3f7fb8 55%,#5b93c4 100%)}
.video .play{position:absolute;left:181px;top:118px;width:56px;height:40px;background:#e52d27;border-radius:10px}
.video .play:after{content:"";position:absolute;left:22px;top:11px;border-left:16px solid #fff;border-top:9px solid transparent;border-bottom:9px solid transparent}

/* courts band */
.band{left:0;width:1200px}
.courts-ghost-a{left:97px;top:1258px;font-size:62px;color:rgba(255,255,255,.12)}
.courts-ghost-b{left:97px;top:1434px;font-size:62px;color:rgba(255,255,255,.12)}
.courts-title{left:97px;top:1326px;font-size:32px;color:#fff}
.courts-text{left:97px;top:1384px;width:620px;color:#fff;font-size:14px;line-height:25px}
.ball-photo{left:786px;top:1212px;width:314px;height:314px;border-radius:50%;border:6px solid #fff;box-shadow:0 4px 14px rgba(0,0,0,.25);background:linear-gradient(180deg,#16251a 0%,#24382a 55%,#3a2a28 85%,#6a2e2c 100%)}

/* facilities grid */
.grid{left:99px;top:1683px;width:1001px;height:460px;display:grid;grid-template-columns:repeat(3,1fr);grid-template-rows:repeat(2,1fr);border:1px solid var(--line)}
.cell{position:relative;text-align:center;padding:36px 34px 0;background:#fff}
.cell h3{font-size:20px;color:#222;letter-spacing:1px}
.cell p{margin-top:18px;font-size:12.5px;line-height:23px;color:var(--muted)}
.cell .more{display:inline-block;margin-top:16px;font-size:11px;font-weight:700;color:var(--green);text-transform:uppercase;text-decoration:none}
.photo-courts{background:linear-gradient(180deg,#6b8fc0 0%,#b9c7d6 45%,#2f5d8f 62%,#3d6fa0 100%)}
.photo-house{background:linear-gradient(180deg,#dfe4ea 0%,#c8ccd0 40%,#6d6f72 75%,#8d8f91 100%)}
.photo-pool{background:linear-gradient(180deg,#6e7a7a 0%,#4b6f8d 35%,#1a6fb8 60%,#2a8bd6 100%)}

/* testimonials */
.member-photo{left:100px;top:2280px;width:314px;height:314px;border-radius:50%;border:6px solid #fff;box-shadow:0 4px 14px rgba(0,0,0,.25);background:linear-gradient(180deg,#1f2a22 0%,#3a4a3c 45%,#8a8f88 75%,#4a5a48 100%)}
.testi-ghost{left:509px;top:2320px;font-size:60px;color:rgba(255,255,255,.13)}
.testi-name{left:509px;top:2380px;font-size:33px;color:#fff}
.testi-text{left:509px;top:2432px;width:590px;color:#fff;font-size:14px;line-height:25px;font-style:italic}
.arrows{left:1020px;top:2548px;display:flex;gap:14px}
.arrows span{width:32px;height:32px;border-radius:50%;background:#111;display:flex;align-items:center;justify-content:center}

/* coaches */
.coaches-title{left:99px;top:2680px;font-size:32px;color:#111}
.coaches-text{left:99px;top:2734px;font-size:12.5px;color:var(--muted)}
.coach{top:2793px;width:478px;height:208px}
.coach .pic{position:absolute;left:0;top:0;width:201px;height:208px}
.coach .share{position:absolute;left:0;bottom:0;width:201px;height:40px;display:flex}
.coach .share span{flex:1}
.coach .card{position:absolute;left:201px;top:16px;width:277px;height:178px;background:#fff;box-shadow:0 2px 12px rgba(0,0,0,.12);padding:24px 28px}
.coach h4{font-size:17px;letter-spacing:1px}
.coach .role{font-size:12px;color:var(--green);font-weight:700;margin-top:10px}
.coach p{font-size:11.5px;line-height:20px;color:var(--muted);margin-top:14px}
.pic-a{background:linear-gradient(180deg,#5e8c5a 0%,#a9b99a 40%,#dcdcd6 70%,#b8b8b4 100%)}
.pic-b{background:linear-gradient(180deg,#7aa06a 0%,#b8c4a8 40%,#dcd8cc 70%,#9a9a94 100%)}
.s1{background:#3b5998}.s2{background:#2aa3ef}.s3{background:#dc4a38}

/* footer */
.footer-brand{left:98px;top:3196px;display:flex;flex-direction:column;align-items:center;color:#fff}
.footer-brand .brand-mark{width:84px;height:84px;border-width:4px}
.footer-brand .brand-name{font-size:36px;margin-top:10px}
.f-head{font-size:15px;font-weight:700;color:#fff;text-transform:uppercase}
.follow{left:402px;top:3212px}
.socials{left:402px;top:3262px;display:flex;gap:12px}
.socials span{width:42px;height:42px;border:2px solid #fff;border-radius:50%}
.news{left:698px;top:3212px}
.news-text{left:698px;top:3250px;color:#fff;font-size:13px}
.news-input{left:698px;top:3288px;width:284px;height:40px;border:1px solid #ccc;color:#fff;font-size:13px;padding:11px 12px}
.news-btn{left:992px;top:3288px;width:108px;height:40px;background:var(--green);color:#fff;font-size:11px;font-weight:700;display:flex;align-items:center;justify-content:center}
.rule{left:98px;top:3387px;width:1002px;height:1px;background:#444}
.copy{left:0;top:3418px;width:1200px;text-align:center;color:#fff;font-size:13px}
</style>
</head>
<body>

<header class="abs hero">
  <svg class="hero-bg" width="1200" height="640" viewBox="0 0 1200 640" role="img" aria-label="Photo of a tennis player returning a ball on a clay court with trees behind">
    <defs>
      <linearGradient id="heroFill" x1="0" y1="0" x2="0" y2="1">
        <stop offset="0" stop-color="#2d4a2e"/>
        <stop offset="0.55" stop-color="#4c6a45"/>
        <stop offset="0.82" stop-color="#5d3a34"/>
        <stop offset="1" stop-color="#7a3b33"/>
      </linearGradient>
    </defs>
    <polygon points="0,0 1200,0 1200,570 0,630" fill="url(#heroFill)"/>
    <polygon points="0,0 1200,0 1200,570 0,630" fill="rgba(0,0,0,.15)"/>
  </svg>
  <div class="abs brand"><span class="brand-mark"></span><span class="brand-name">Willow Fen</span></div>
  <nav class="abs nav">
    <a href="#">HOME</a><a href="#">ABOUT US</a><a href="#">COURTS</a><a href="#">SCHEDULE</a><a href="#">CONTACT</a>
    <svg class="search" width="16" height="16" viewBox="0 0 16 16"><circle cx="6.5" cy="6.5" r="5" stroke="#fff" stroke-width="2" fill="none"/><line x1="10.5" y1="10.5" x2="15" y2="15" stroke="#fff" stroke-width="2.4"/></svg>
  </nav>
  <h1 class="abs heading hero-title">Sports for<br>healthy lifetime</h1>
  <div class="abs heading hero-ghost">Tennis courts</div>
  <div class="abs dots"><span></span><span class="on"></span><span></span><span></span></div>
</header>

<div class="abs weather">
  <div class="heading city">Florida</div>
  <div class="country">USA</div>
  <div class="date">28 Apr 2018</div>
  <div class="temp">13°</div>
  <div class="range">15° | 11°</div>
  <svg width="64" height="56" viewBox="0 0 64 56"><path d="M16 34a10 10 0 0 1 2-20 14 14 0 0 1 26 2 9 9 0 0 1 4 18z" fill="none" stroke="#fff" stroke-width="3"/><g stroke="#fff" stroke-width="3" stroke-linecap="round"><line x1="20" y1="42" x2="18" y2="48"/><line x1="30" y1="42" x2="28" y2="48"/><line x1="40" y1="42" x2="38" y2="48"/></g></svg>
</div>

<section>
  <h2 class="abs heading welcome-title">Welcome to Willow Fen</h2>
  <p class="abs body-text welcome-text">Nemo enim ipsam voluptatem quia voluptas sit aspernatur aut odit aut fugit, sed quia consequuntur magni dolores eos qui ratione voluptatem sequi nesciunt. Neque porro quisquam est, qui dolorem ipsum quia dolor sit amet, consectetur, adipisci velit, sed quia non numquam eius modi tempora incidunt ut labore et dolore magnam aliquam quaerat voluptatem. Ut enim ad minima veniam, quis nostrum exercitationem ullam corporis suscipit laboriosam commodi.</p>
  <a class="abs btn welcome-btn" href="#">Read more
    <svg width="14" height="14" viewBox="0 0 14 14"><circle cx="7" cy="7" r="7" fill="#fff"/><path d="M5 4l3.5 3L5 10" stroke="#1f6b3d" stroke-width="2" fill="none"/></svg></a>
  <div class="abs video" role="img" aria-label="Video still of a player stretching for a forehand on a blue hard court"><span class="play"></span></div>
</section>

<section>
  <svg class="abs band" style="top:1160px" width="1200" height="430" viewBox="0 0 1200 430">
    <polygon points="0,8 1200,70 1200,330 0,424" fill="#1f6b3d"/>
  </svg>
  <div class="abs heading courts-ghost-a">Willow Fen</div>
  <h2 class="abs heading courts-title">Our courts</h2>
  <p class="abs courts-text">Nemo enim ipsam voluptatem quia voluptas sit aspernatur aut odit aut fugit, sed quia consequuntur magni dolores eos qui ratione voluptatem sequi nesciunt.</p>
  <div class="abs heading courts-ghost-b">Courts</div>
  <div class="abs ball-photo" role="img" aria-label="Close-up photo of a tennis ball resting on a court line"></div>
</section>

<section class="abs grid">
  <div class="photo-courts" role="img" aria-label="Photo of the outdoor tennis courts under a cloudy sky"></div>
  <div class="cell">
    <h3 class="heading">Swimming pool</h3>
    <p>Nemo enim ipsam voluptatem voluptas sit quia aspernatur aut odit aut fugit, sed quia aut conse quuntur magni dolores eos</p>
    <a class="more" href="#">Read more ›</a>
  </div>
  <div class="photo-house" role="img" aria-label="Rendering of the two-storey clubhouse"></div>
  <div class="cell">
    <h3 class="heading">Tennis courts</h3>
    <p>Nemo enim ipsam voluptatem voluptas sit quia aspernatur aut odit aut fugit, sed quia aut conse quuntur magni dolores eos</p>
    <a class="more" href="#">Read more ›</a>
  </div>
  <div class="photo-pool" role="img" aria-label="Photo of the club swimming pool"></div>
  <div class="cell">
    <h3 class="heading">Clubhouse</h3>
    <p>Nemo enim ipsam voluptatem voluptas sit quia aspernatur aut odit aut fugit, sed quia aut conse quuntur magni dolores eos</p>
    <a class="more" href="#">Read more ›</a>
  </div>
</section>

<section>
  <svg class="abs band" style="top:2230px" width="1200" height="430" viewBox="0 0 1200 430">
    <polygon points="0,46 1200,6 1200,424 0,322" fill="#1f6b3d"/>
    <text x="890" y="340" font-family="Georgia,serif" font-size="110" fill="rgba(255,255,255,.15)">”</text>
  </svg>
  <div class="abs member-photo" role="img" aria-label="Photo of a club member holding a racquet at night"></div>
  <div class="abs heading testi-ghost">Testimonials</div>
  <h3 class="abs heading testi-name">Marcus Hale</h3>
  <p class="abs testi-text">Nemo enim ipsam voluptatem quia voluptas sit aspernatur aut odit aut fugit, sedfed quia consequuntur magni dolores eos qui ratione voluptatem sequi nesciunt. Neque porro quisquam est, qui dolorem ipsum quia dolor sit amet</p>
  <div class="abs arrows">
    <span><svg width="12" height="12" viewBox="0 0 12 12"><path d="M8 2L4 6l4 4" stroke="#fff" stroke-width="2" fill="none"/></svg></span>
    <span><svg width="12" height="12" viewBox="0 0 12 12"><path d="M4 2l4 4-4 4" stroke="#fff" stroke-width="2" fill="none"/></svg></span>
  </div>
</section>

<section>
  <h2 class="abs heading coaches-title">Our club coaches</h2>
  <p class="abs coaches-text">Nemo enim ipsam voluptatem quia voluptas sit aspernatur aut odit aut fugit nesciunt.</p>
  <div class="abs coach" style="left:99px">
    <div class="pic pic-a" role="img" aria-label="Photo of a male trainer holding a racquet"></div>
    <div class="share"><span class="s1"></span><span class="s2"></span><span class="s3"></span></div>
    <div class="card">
      <h4 class="heading">Owen Pryce</h4>
      <div class="role">Trainer</div>
      <p>Neque porro quisquam est, qui dolorem ipsum quia dolor sit amet, consectetur, adipisci velit, sed quia non</p>
    </div>
  </div>
  <div class="abs coach" style="left:622px">
    <div class="pic pic-b" role="img" aria-label="Photo of a female trainer holding a racquet"></div>
    <div class="share"><span class="s1"></span><span class="s2"></span><span class="s3"></span></div>
    <div class="card">
      <h4 class="heading">Nina Castell</h4>
      <div class="role">Trainer</div>
      <p>Neque porro quisquam est, qui dolorem ipsum quia dolor sit amet, consectetur, adipisci velit, sed quia non</p>
    </div>
  </div>
</section>

<footer>
  <svg class="abs band" style="top:3080px" width="1200" height="388" viewBox="0 0 1200 388">
    <polygon points="0,10 1200,90 1200,388 0,388" fill="#1b1b1b"/>
  </svg>
  <div class="abs footer-brand"><span class="brand-mark"></span><span class="brand-name">Willow Fen</span></div>
  <div class="abs f-head follow">Follow us on</div>
  <div class="abs socials"><span></span><span></span><span></span><span></span></div>
  <div class="abs f-head news">Newsletter subscribe</div>
  <div class="abs news-text">Stay in touch with coupons and informative articles.</div>
  <div class="abs news-input">Enter Email</div>
  <div class="abs news-btn">SUBSCRIBE</div>
  <div class="abs rule"></div>
  <div class="abs copy">Copyrights © 2018 Harlow Athletics. All Rights Reserved.</div>
</footer>

</body>
</html>
```